DMW Snack Box for Printed Packaging

This is a HVZ style 2 piece snack box. We have a jpeg logo and need it to be applied to the box along with some form of creative design. I have uploaded the keyline for the package. Please lay out the logo and design on this. Please bear in mind that the carton will be folded and appear like the photo which is also uploaded

Target Market(s)

General consumers in St. Lucia in the caribbean

Colors
EB3D1F
EC4F4E
F09395
F8D3D4
FCEDEE

```html
<!DOCTYPE html>
<html lang="en">
<head>
<meta charset="utf-8">
<title>DMW Snack Box – Panel Artwork</title>
<link rel="stylesheet" href="https://fonts.googleapis.com/css2?family=Archivo:wght@800&family=Great+Vibes&display=swap">
<style>
  :root {
    --brand-red: #EB3D1F;
    --brand-red-deep: #D91E18;
    --coral: #EC4F4E;
    --pink: #F09395;
    --blush: #F8D3D4;
    --paper: #FCEDEE;
    --white: #FFFFFF;
    --ink: #1B1B1B;
    --backdrop: #D8D9DB;
  }
  html, body {
    margin: 0;
    width: 1200px;
    height: 1200px;
    overflow: hidden;
    background: var(--backdrop);
  }
  .canvas {
    width: 1200px;
    height: 1200px;
    display: flex;
    align-items: center;
    justify-content: center;
  }
  .box-artwork { display: block; }
  .panel-red { fill: var(--brand-red-deep); }
  .panel-white { fill: var(--white); }
  .fold-line { stroke: rgba(0,0,0,0.12); stroke-width: 1; }
  .tagline {
    font-family: "Great Vibes", cursive;
    font-size: 48px;
  }
  .tagline--light { fill: var(--white); }
  .tagline--dark { fill: var(--ink); }
  .brand-name {
    font-family: "Archivo", sans-serif;
    font-weight: 800;
    font-size: 44px;
    fill: var(--brand-red);
    letter-spacing: -0.5px;
  }
</style>
</head>
<body>
<main class="canvas">
  <svg class="box-artwork" width="1080" height="420" viewBox="0 0 1080 420" role="group" aria-label="DMW snack box end panel and front panel">
    <defs>
      <linearGradient id="mascot-tones" x1="0" y1="0" x2="0" y2="1">
        <stop offset="0" stop-color="#F4F4F6"/>
        <stop offset="0.6" stop-color="#E9E2E6"/>
        <stop offset="1" stop-color="#E24A3C"/>
      </linearGradient>
    </defs>

    <!-- end panel + front panel base -->
    <rect class="panel-white" x="0" y="0" width="1080" height="420"/>

    <!-- left red sweep across end panel onto front -->
    <polygon class="panel-red" points="0,0 560,0 250,420 0,420"/>

    <!-- right red food-doodle area -->
    <polygon class="panel-red" points="1080,40 1080,420 760,420" role="img" aria-label="Red panel with white line doodles of fast food: fries, burgers, pizza, drinks, chicken and desserts"/>

    <!-- fold between end and front panel -->
    <line class="fold-line" x1="360" y1="0" x2="360" y2="420"/>

    <!-- end panel tagline -->
    <text class="tagline tagline--light" x="60" y="230">Best Choice !</text>

    <!-- mascot area -->
    <rect x="578" y="100" width="110" height="210" rx="18" fill="url(#mascot-tones)" role="img" aria-label="Cartoon chef rooster mascot giving a thumbs up"/>

    <!-- brand name -->
    <text class="brand-name" x="700" y="180">SNAP</text>
    <text class="brand-name" x="700" y="228">HOUR</text>

    <!-- front panel tagline -->
    <text class="tagline tagline--dark" x="600" y="385">Best Choice !</text>
  </svg>
</main>
</body>
</html>
```